Business card design Needed for new logo / Construction business, home extensions and new builds

We need a business card design using our new logo files which i will attach to this project :)

We are a small construction business specialising in home extensions, new builds and property development. We are very ambitious and would appreciate professional and elegant designs for our new business card.

Very serious about using the services on MakerQuarry and recently acquired our new logo from here :)

Please get involved, i will feedback when i can as i am very busy but can respond daily, thanks

Target Market(s)

People that want to build onto their houses, new building developments or adding too their existing property

Industry/Entity Type

Construction

Contact Information for Business Card

Renwick Tolliver Construction, Lionel Ashby (Managing Director), Tel 07822254961, email - info@renwick-tolliver, www.renwick-tolliver.co.uk

Colors

Designer to choose colors to be used in the design.

Requirements
Must have
• I like a deep grey on the back please. A lot of you have provided black from and back, try mixing things up a little. The black looks cool 😎 Thanks

```html
<!DOCTYPE html>
<html lang="en">
<head>
<meta charset="utf-8">
<title>Renwick Tolliver Construction – Business Card</title>
<link href="https://fonts.googleapis.com/css2?family=Lato:wght@400;700&display=swap" rel="stylesheet">
<style>
  :root {
    --stage: #1c1c1d;
    --card-grey: #474747;
    --gold: #d9a53a;
    --text-light: #e4e4e4;
    --ink: #1a1a1a;
  }
  * { box-sizing: border-box; margin: 0; padding: 0; }
  html, body { width: 1200px; height: 982px; overflow: hidden; }
  body {
    background: var(--stage);
    font-family: "Lato", Arial, sans-serif;
    display: flex;
    flex-direction: column;
    align-items: center;
    justify-content: center;
    gap: 64px;
  }
  .card {
    position: relative;
    width: 620px;
    height: 354px;
    border-radius: 22px;
    background: var(--card-grey);
    overflow: hidden;
  }

  /* Front */
  .card-front {
    display: flex;
    align-items: center;
    justify-content: center;
  }
  .front-lockup {
    display: flex;
    flex-direction: column;
    align-items: center;
    gap: 26px;
    text-align: center;
  }
  .front-lockup .mark-square {
    width: 34px;
    height: 34px;
    background: var(--gold);
  }
  .front-name {
    color: var(--gold);
    font-weight: 700;
    font-size: 30px;
    line-height: 1.3;
    letter-spacing: 3px;
    text-transform: uppercase;
  }

  /* Back */
  .back-brand {
    position: absolute;
    top: 40px;
    right: 40px;
    display: flex;
    align-items: center;
    gap: 8px;
    color: var(--gold);
    font-weight: 700;
    font-size: 13px;
    letter-spacing: 1.5px;
    text-transform: uppercase;
  }
  .back-brand .mark-square {
    width: 12px;
    height: 12px;
    background: var(--gold);
  }
  .person {
    position: absolute;
    top: 118px;
    left: 32px;
    width: 272px;
    text-align: right;
  }
  .person-name {
    color: var(--gold);
    font-weight: 700;
    font-size: 29px;
    letter-spacing: 0.5px;
    text-transform: uppercase;
  }
  .person-title {
    color: var(--text-light);
    font-size: 17px;
    margin-top: 6px;
  }
  .divider {
    position: absolute;
    top: 116px;
    left: 322px;
    width: 1.5px;
    height: 100px;
    background: var(--gold);
  }
  .contact-list {
    position: absolute;
    top: 124px;
    left: 342px;
    list-style: none;
    color: var(--text-light);
    font-size: 17px;
    line-height: 30px;
  }
  .contact-list li { display: flex; align-items: center; gap: 10px; }
  .contact-list svg { width: 14px; height: 14px; fill: var(--gold); flex: none; }

  .address-band {
    position: absolute;
    left: 0;
    bottom: 0;
    width: 100%;
    height: 62px;
  }
  .address-band svg.band { position: absolute; inset: 0; width: 100%; height: 100%; }
  .address-text {
    position: absolute;
    left: 150px;
    top: 20px;
    display: flex;
    align-items: center;
    gap: 8px;
    color: var(--ink);
    font-size: 16px;
    letter-spacing: 0.5px;
    text-transform: uppercase;
  }
  .address-text svg { width: 12px; height: 16px; fill: var(--ink); }
</style>
</head>
<body>

  <section class="card card-front">
    <div class="front-lockup">
      <span class="mark-square"></span>
      <p class="front-name">Renwick Tolliver<br>Construction</p>
    </div>
  </section>

  <section class="card card-back">
    <div class="back-brand">
      <span class="mark-square"></span>
      <span>Renwick Tolliver</span>
    </div>

    <div class="person">
      <h1 class="person-name">Lionel Ashby</h1>
      <p class="person-title">Managing Director</p>
    </div>

    <div class="divider"></div>

    <ul class="contact-list">
      <li>
        <svg viewBox="0 0 24 24"><path d="M6.6 10.8a15 15 0 0 0 6.6 6.6l2.2-2.2a1 1 0 0 1 1-.25 11.4 11.4 0 0 0 3.6.57 1 1 0 0 1 1 1V20a1 1 0 0 1-1 1A17 17 0 0 1 3 4a1 1 0 0 1 1-1h3.5a1 1 0 0 1 1 1c0 1.25.2 2.45.57 3.57a1 1 0 0 1-.25 1z"/></svg>
        07822254961
      </li>
      <li>
        <svg viewBox="0 0 24 24"><path d="M2 5h20v14H2z M2 5l10 8 10-8" fill="none" stroke="#d9a53a" stroke-width="2"/></svg>
        info@renwick-tolliver.co.uk
      </li>
      <li>
        <svg viewBox="0 0 24 24"><circle cx="12" cy="12" r="9" fill="none" stroke="#d9a53a" stroke-width="2"/><path d="M3 12h18M12 3c3 3 3 15 0 18M12 3c-3 3-3 15 0 18" fill="none" stroke="#d9a53a" stroke-width="1.5"/></svg>
        renwick-tolliver.co.uk
      </li>
    </ul>

    <div class="address-band">
      <svg class="band" viewBox="0 0 620 62" preserveAspectRatio="none">
        <defs>
          <linearGradient id="goldBand" x1="0" x2="1" y1="0" y2="0">
            <stop offset="0" stop-color="#b47a16"/>
            <stop offset="0.5" stop-color="#f6d98a"/>
            <stop offset="1" stop-color="#c8891f"/>
          </linearGradient>
          <linearGradient id="silverCorner" x1="0" x2="1" y1="0" y2="1">
            <stop offset="0" stop-color="#8f9499"/>
            <stop offset="0.6" stop-color="#e9ebed"/>
            <stop offset="1" stop-color="#c3c6c9"/>
          </linearGradient>
        </defs>
        <polygon points="0,0 520,0 545,62 0,62" fill="url(#goldBand)"/>
        <polygon points="520,0 620,0 620,62 545,62" fill="url(#silverCorner)"/>
      </svg>
      <div class="address-text">
        <svg viewBox="0 0 12 16"><path d="M6 0a6 6 0 0 0-6 6c0 4.5 6 10 6 10s6-5.5 6-10a6 6 0 0 0-6-6zm0 8.5A2.5 2.5 0 1 1 6 3.5a2.5 2.5 0 0 1 0 5z"/></svg>
        Renwick Tolliver Construction
      </div>
    </div>
  </section>

</body>
</html>
```